Slow Winter Song. A CD of beautiful 17th century music for lute played by a world famous lutenist.

Hi designers,
My name is Ollie Pellicott and I am an international lute player in need of a CD cover design. I am blind, so will be relying on other people's eyes and descriptions during the process, including yours! Are you up for the challenge?
My CD is called Slow Winter Song. It's beautiful lute music from the 17th century, very intimate and carming, but also very powerful.
I would like you to use the attached image, and find a way to include the following text in a tasteful way:
The text for the front cover is as follows:
Slow Winter Song
Oliver Pellicott - lute and theorbo
Music by Harcrane, Fennimore, Brackley, Tarn, Cavallenti and Ruhlendorf.
Here is a viewora link to some of the music I play, which should give you an idea:
www.viewora.net/olliepellicott1
Here is a link to my website, where you can see the covers of my other CDs, and get more information about me:
www.oliverpellicott.net
I'm excited to receive your design and ideas.
Best wishes
Ollie

```html
<!DOCTYPE html>
<html lang="en">
<head>
<meta charset="utf-8">
<title>Slow Winter Song – Oliver Pellicott</title>
<link href="https://fonts.googleapis.com/css2?family=Pinyon+Script&family=Didact+Gothic&display=swap" rel="stylesheet">
<style>
  :root {
    --cover-dark: #0d0806;
    --cover-brown: #2a1a10;
    --satin-red: #b0122a;
    --satin-pink: #e0587a;
    --lute-wood: #c9a46a;
    --text-white: #ffffff;
  }
  html, body {
    margin: 0;
    padding: 0;
    width: 1200px;
    height: 1200px;
    overflow: hidden;
    background: var(--cover-dark);
  }
  .cd-cover {
    position: relative;
    width: 1200px;
    height: 1200px;
    overflow: hidden;
  }
  .cover-photo {
    position: absolute;
    inset: 0;
    width: 1200px;
    height: 1200px;
  }
  .cover-title {
    position: absolute;
    top: 40px;
    right: 56px;
    margin: 0;
    font-family: "Pinyon Script", cursive;
    font-weight: 400;
    font-size: 108px;
    line-height: 1.3;
    color: var(--text-white);
    white-space: nowrap;
  }
  .cover-credits {
    position: absolute;
    top: 496px;
    right: 47px;
    text-align: right;
    font-family: "Didact Gothic", sans-serif;
    font-size: 36px;
    line-height: 43px;
    color: var(--text-white);
  }
  .performer {
    margin: 0 0 45px 0;
  }
  .composers {
    margin: 0;
    padding: 0;
    list-style: none;
  }
</style>
</head>
<body>
  <main class="cd-cover">
    <svg class="cover-photo" role="img" aria-label="Still life photograph: a lute leaning against a goblet of red wine and a brass vase with ivy and pink hydrangea, on draped red satin against a dark background" viewBox="0 0 1200 1200" xmlns="http://www.w3.org/2000/svg">
      <defs>
        <linearGradient id="backdrop" x1="0" y1="0" x2="0" y2="1">
          <stop offset="0" stop-color="var(--cover-dark)"/>
          <stop offset="0.5" stop-color="var(--cover-brown)"/>
          <stop offset="0.62" stop-color="#3a1410"/>
          <stop offset="0.78" stop-color="var(--satin-red)"/>
          <stop offset="0.88" stop-color="var(--satin-pink)"/>
          <stop offset="1" stop-color="#8c0e20"/>
        </linearGradient>
        <radialGradient id="lute-glow" cx="0.28" cy="0.7" r="0.3">
          <stop offset="0" stop-color="var(--lute-wood)" stop-opacity="0.85"/>
          <stop offset="1" stop-color="var(--lute-wood)" stop-opacity="0"/>
        </radialGradient>
      </defs>
      <rect width="1200" height="1200" fill="url(#backdrop)"/>
      <rect width="1200" height="1200" fill="url(#lute-glow)"/>
    </svg>

    <h1 class="cover-title">Slow Winter Song</h1>

    <section class="cover-credits">
      <p class="performer">Oliver Pellicott<br>LUTE and THEORBO</p>
      <div class="music-by">Music by:</div>
      <ul class="composers">
        <li>Harcrane</li>
        <li>Fennimore</li>
        <li>Brackley</li>
        <li>Tarn</li>
        <li>Cavallenti</li>
        <li>Ruhlendorf</li>
      </ul>
    </section>
  </main>
</body>
</html>
```